Business Card Design

New business card design

Target Market(s)

Residential & Commercial Property Managers

Industry/Entity Type

Plumbing Services

Contact Information for Business Card

Name - Rowan Keddle, title - Director, Phone Number - 0431 286 517, email - rowan@tbk-plumbing.com.au, Company ABN - 73 215 904 386,

Font styles to use
Sans Serif

Colors
0054AA
0677BA
7BADD7
CADEEF
E8F1F8

```html
<!DOCTYPE html>
<html lang="en">
<head>
<meta charset="utf-8">
<title>TBK Plumbing Services – Business Card</title>
<link rel="stylesheet" href="https://fonts.googleapis.com/css2?family=Arimo:wght@400;700&display=swap">
<style>
  :root {
    --backdrop: #3d3d3d;
    --card-white: #ffffff;
    --brand-blue: #03adee;
    --ink-dark: #1c232b;
    --ink-text: #2b2f33;
    --divider: #cfd3d6;
  }
  * { box-sizing: border-box; margin: 0; padding: 0; }
  html, body {
    width: 1200px; height: 803px; overflow: hidden;
    background: var(--backdrop);
    font-family: "Arimo", Arial, sans-serif;
  }
  .canvas {
    position: relative; width: 1200px; height: 803px;
  }
  .card {
    position: absolute; top: 249px;
    width: 510px; height: 305px;
    border-radius: 22px;
    overflow: hidden;
    box-shadow: 0 18px 30px rgba(0,0,0,0.45);
  }

  /* Front */
  .card-front { left: 50px; background: var(--card-white); }
  .front-logo {
    position: absolute; left: 40px; top: 92px; width: 200px;
    color: var(--ink-dark); font-weight: 400;
  }
  .logo-mark { display: flex; align-items: center; gap: 8px; }
  .logo-name { font-size: 64px; letter-spacing: 2px; line-height: 1; }
  .logo-dot { width: 12px; height: 12px; border-radius: 50%; background: var(--brand-blue); }
  .logo-tagline { font-size: 9px; letter-spacing: 7px; margin-top: 8px; padding-left: 4px; }
  .front-divider {
    position: absolute; left: 262px; top: 70px; width: 1px; height: 120px;
    background: linear-gradient(to bottom, transparent, var(--divider), transparent);
  }
  .contact { position: absolute; left: 285px; top: 72px; color: var(--ink-text); }
  .contact-name { font-weight: 700; font-size: 20px; color: var(--ink-dark); }
  .contact-title { font-size: 12px; color: var(--brand-blue); margin-bottom: 12px; }
  .contact-line { display: flex; align-items: center; gap: 7px; font-size: 12px; line-height: 18px; }
  .contact-line svg { width: 10px; height: 10px; fill: var(--ink-dark); }
  .contact-abn { font-size: 12px; line-height: 18px; }
  .front-band {
    position: absolute; left: 0; right: 0; bottom: 14px; height: 34px;
    display: flex;
  }
  .band-dark {
    flex: 0 0 74%; background: var(--ink-dark); color: #fff;
    font-size: 13px; font-weight: 700; letter-spacing: 3px;
    display: flex; align-items: center; padding-left: 40px;
  }
  .band-blue { flex: 1; background: var(--brand-blue); position: relative; }
  .band-blue::before {
    content: ""; position: absolute; left: -9px; top: 8px;
    width: 18px; height: 18px; border-radius: 50%;
    background: var(--brand-blue); border: 2px solid #fff;
  }

  /* Back */
  .card-back { left: 640px; background: var(--brand-blue); }
  .back-logo {
    position: absolute; left: 0; right: 0; top: 90px;
    text-align: center; color: var(--ink-dark); font-weight: 400;
  }
  .back-logo .logo-mark { justify-content: center; gap: 12px; }
  .back-logo .logo-name { font-size: 96px; letter-spacing: 4px; }
  .back-logo .logo-dot { width: 18px; height: 18px; }
  .back-logo .logo-tagline { font-size: 13px; letter-spacing: 14px; margin-top: 12px; }
</style>
</head>
<body>
<main class="canvas">
  <section class="card card-front" aria-label="Business card front">
    <div class="front-logo">
      <div class="logo-mark"><span class="logo-name">tbk</span><span class="logo-dot"></span></div>
      <div class="logo-tagline">plumbing services</div>
    </div>
    <div class="front-divider"></div>
    <div class="contact">
      <div class="contact-name">Rowan Keddle</div>
      <div class="contact-title">Director</div>
      <div class="contact-line">
        <svg viewBox="0 0 10 10"><path d="M2 0h2l1 2.5-1.3 1a6 6 0 0 0 2.8 2.8l1-1.3L10 6v2a2 2 0 0 1-2 2A8 8 0 0 1 0 2a2 2 0 0 1 2-2z"/></svg>
        <span>0431 286 517</span>
      </div>
      <div class="contact-line">
        <svg viewBox="0 0 10 10"><path d="M0 2h10v6H0z M0 2l5 3.5L10 2" fill="none" stroke="#1c232b" stroke-width="1.2"/></svg>
        <span>rowan@tbk-plumbing.com.au</span>
      </div>
      <div class="contact-abn">ABN - 73 215 904 386</div>
    </div>
    <div class="front-band">
      <div class="band-dark">www.tbk-plumbing.com</div>
      <div class="band-blue"></div>
    </div>
  </section>

  <section class="card card-back" aria-label="Business card back">
    <div class="back-logo">
      <div class="logo-mark"><span class="logo-name">tbk</span><span class="logo-dot"></span></div>
      <div class="logo-tagline">plumbing services</div>
    </div>
  </section>
</main>
</body>
</html>
```